A website where experts collaborate on your project

I am building a new website where experts (yes, like designers) collaborate on projects with the project owner. More minds = more collaboration = better end product. Please see Pelmora(dot)com for a quick landing page I created for collaborating on presentations (although there will be many project types offered)

I am looking for a DESIGNER LONG TERM, but for now, just need initial mock ups to show the web programmers.

I have 21 Word documents loosely designed, what I would like to see here is a theme. Please DO NOT GO OFF WHAT YOU CURRENTLY SEE AT PELMORA. What is up now is only a quick landing page.

You can view a Word doc of the homepage here:
https://www.filevanta.com/s/qx83kdm2/home.docx?dl=0

WHAT AM I LOOKING FOR?
A clean, well designed theme.

Here is a link to the logo:
https://www.filevanta.com/s/mr47tpz9/logo%20-%20horizontal.tif?dl=0
-----------------------------------------
Here are a few sites I like the design of and what I like about them:
www.quenbrook.com-all around my favorite, beautiful graphics, clean layout, bold use of colors on a dark background
Ravelto.com- clean layout, The use of humans and bubble style elements.
Mintharbor.com :) clean, bold, unique pop art style but professional
plumevault.com - From the unique colors and artwork and the ability of that art to not interfere with the important elements of the site
sparkwidgets.com-clean, nice colors, well organized and separated sections.
www.dunmereco.com-love the font, use of colors and sectionalized style

All in all, I am not picky and open to so many styles. I would ultimately like the designer I pick to design all 21 pages.
Updates

Hello everyone,Moving forward, I would like you all to pay special attention to the section in my brief titled "Here are a few sites I like the design of and what I like about them". Please see below, I handpicked each one of these as sites I really like. Thank you.Here are a few sites I like the design of and what I like about them:Ravelto.com- clean layout, The use of humans and bubble style elements.Mintharbor.com :) clean, bold, unique pop art style but professionalwriteraccess.com - From the unique colors and artwork and the ability of that art to not interfere with the important elements of the sitegrowthgeeks.com-clean, nice colors, well organized and separated sections.www.dunmereco.com-love the font, use of colors and sectionalized stylewww.quenbrook.com-beautiful graphics, clean layout, bold use of colors----------------------------------------- Added Tuesday, November 24, 2015

I updated the homepage, you can see it here:https://www.dropbox.com/s/kwlkbsookq3cg2m/1new%20homepage.docx?dl=0I am modeling it after my favorite designed site: triplelift.comI love the dark colors with the orange glowing style boldness of the buttons. It's real clean too. Added Tuesday, November 24, 2015

Target Market(s)

small business owners, marketers, freelancer writers, graphic designers,

Industry/Entity Type

Building

Number of Pages Required

5+ page

Requirements
Must have
• I can't think of anything the project must have.
Nice to have
• WHAT AM I LOOKING FOR?
• A clean, well designed theme. I had a designer do a bit of work putting elements together, I found it to be very plain, but I like the Application Page (https://www.filevanta.com/s/jb19ckr3/Pelmora-Website.ai?dl=0)
• Here is a link to the logo:
• https://www.filevanta.com/s/mr47tpz9/logo%20-%20horizontal.tif?dl=0
• Here are a few sites I like the design of and what I like about them:
• Ravelto.com- clean layout, The use of humans and bubble style elements.
• Mintharbor.com :) clean, bold, unique pop art style but professional
• plumevault.com - From the unique colors and artwork and the ability of that art to not interfere with the important elements of the site
• sparkwidgets.com-clean, nice colors, well organized and separated sections.
• www.dunmereco.com-love the font, use of colors and sectionalized style
• www.quenbrook.com-beautiful graphics, clean layout, bold use of colors
• -----------------------------------------
Should not have
• out of the boxed, templated style website. I want this site to be memorable and not look like a thousand others

```html
<!DOCTYPE html>
<html lang="en">
<head>
<meta charset="utf-8">
<title>Pelmora — The Evolution of Feedback</title>
<link href="https://fonts.googleapis.com/css2?family=Open+Sans:wght@400;600;700&display=swap" rel="stylesheet">
<style>
:root{
  --orange:#f39a1f;
  --orange-dark:#e0850f;
  --teal:#4fb3c8;
  --ink:#333333;
  --muted:#666666;
  --light:#f1f3f6;
  --row:#e9e9e9;
  --navy:#1c2430;
  --footer:#2f3032;
  --white:#ffffff;
}
*{margin:0;padding:0;box-sizing:border-box}
html,body{width:1200px;height:2317px;overflow:hidden;background:var(--white)}
body{font-family:"Open Sans",Arial,sans-serif;color:var(--ink);position:relative}
.abs{position:absolute}

/* Hero */
.hero{left:0;top:0;width:1200px;height:670px}
.hero-photo{position:absolute;inset:0;width:1200px;height:670px}
.brand{left:97px;top:40px;display:flex;align-items:center;gap:14px}
.brand-name{font-size:34px;font-weight:600;color:var(--orange);letter-spacing:-.5px}
.brand-dot{width:30px;height:30px;border-radius:50%;background:var(--orange)}
.menu{left:1060px;top:40px;width:28px}
.menu span{display:block;height:5px;background:var(--white);border-radius:2px;margin-bottom:5px}
.hero-title{left:0;width:1200px;top:205px;text-align:center;color:var(--white);font-size:43px;font-weight:700;letter-spacing:.5px}
.hero-sub{left:0;width:1200px;top:290px;text-align:center;color:var(--white);font-size:31px;line-height:53px;font-weight:600}
.btn-ghost{top:448px;width:232px;height:60px;border:2px solid var(--white);color:var(--white);font-size:21px;display:flex;align-items:center;justify-content:center}
.arrow{top:305px;color:var(--white);font-size:34px;font-weight:700}

/* How it works */
.how{left:0;top:640px;width:1200px;height:520px;background:linear-gradient(180deg,#eef1f5,#f6f8fa 60%,#ffffff)}
.how-title{left:0;width:1200px;top:742px;text-align:center;color:var(--orange);font-size:29px;font-weight:600}
.how-rule{left:408px;top:801px;width:384px;height:2px;background:var(--teal)}
.how-sub{left:0;width:1200px;top:840px;text-align:center;color:#555;font-size:16px;font-weight:600}
.step{top:925px;width:260px;text-align:center}
.step svg{display:block;margin:0 auto}
.step-label{margin-top:12px;font-size:13.5px;font-weight:600;color:#333;line-height:24px}

/* Projects */
.types{left:97px;top:1225px;width:363px}
.types-head{height:55px;background:linear-gradient(180deg,#f7a83a,var(--orange-dark));color:var(--white);font-size:22px;font-weight:600;display:flex;align-items:center;justify-content:center}
.types-item{height:55.5px;margin-top:1.7px;background:linear-gradient(180deg,#f3f3f3,var(--row));display:flex;align-items:center;padding-left:64px;font-size:17px;color:#888;position:relative}
.types-item::before{content:"";position:absolute;left:34px;top:22px;width:11px;height:11px;border:1.5px solid var(--orange);border-radius:50%}
.col-label{top:1222px;width:290px;text-align:center;color:var(--orange);font-size:15px;font-weight:600}
.card-img{top:1270px;width:290px;height:192px;box-shadow:0 1px 3px rgba(0,0,0,.25)}
.card-title{top:1480px;font-size:17.5px;font-weight:600;color:#555}
.card-date{top:1513px;font-size:12.5px;color:var(--orange)}
.card-text{top:1543px;width:300px;font-size:12.5px;line-height:21.5px;color:#666}
.btn-orange{background:var(--orange);color:var(--white);font-size:14px;font-weight:600;display:flex;align-items:center;justify-content:center;gap:8px;box-shadow:0 2px 3px rgba(0,0,0,.2)}
.btn-orange::before{content:"";width:9px;height:9px;border:1.5px solid var(--white);border-radius:50%}

/* Feature band */
.band{left:0;top:1705px;width:1200px;height:510px}
.band-head{top:1830px;font-size:21px;font-weight:600;color:var(--white)}
.band-text{font-size:12.5px;line-height:22px;color:var(--white)}
.benefits{left:695px;top:1948px;list-style:none}
.benefits li{font-size:12.5px;color:var(--white);height:30.5px;padding-left:34px;position:relative}
.benefits li::before{content:"";position:absolute;left:2px;top:4px;width:10px;height:10px;border:1.5px solid var(--white);border-radius:50%}

/* Footer */
.footer{left:0;top:2212px;width:1200px;height:105px;background:var(--footer)}
.copy{left:100px;top:2262px;font-size:13.5px;font-weight:600;color:var(--white)}
.links{left:463px;top:2263px;font-size:13.5px;font-weight:600;color:var(--white)}
.social{top:2253px;width:39px;height:39px;border-radius:3px}
</style>
</head>
<body>

<section class="abs hero">
  <svg class="hero-photo" role="img" aria-label="Business team standing around a meeting table in a bright office" viewBox="0 0 1200 670" preserveAspectRatio="none">
    <defs>
      <linearGradient id="heroFill" x1="0" y1="0" x2="0" y2="1">
        <stop offset="0" stop-color="#6b6f74"/>
        <stop offset=".45" stop-color="#3d4045"/>
        <stop offset="1" stop-color="#1f2124"/>
      </linearGradient>
    </defs>
    <path d="M0 0H1200V640Q600 690 0 640Z" fill="url(#heroFill)"/>
  </svg>
  <div class="abs brand"><span class="brand-name">pelmora</span><span class="brand-dot"></span></div>
  <div class="abs menu"><span></span><span></span><span></span></div>
  <div class="abs arrow" style="left:36px">&#8249;</div>
  <div class="abs arrow" style="left:1136px">&#8250;</div>
  <h1 class="abs hero-title">THE EVOLUTION OF FEEDBACK</h1>
  <p class="abs hero-sub">Improve your ROI and get new ideas by collaborating<br>with Pelmora's experts</p>
  <div class="abs btn-ghost" style="left:313px">POST PROJECT</div>
  <div class="abs btn-ghost" style="left:639px">HOW IT WORKS</div>
</section>

<section class="abs how" style="clip-path:path('M0 0Q600 50 1200 0V520H0Z')"></section>
<h2 class="abs how-title">HOW IT WORKS</h2>
<div class="abs how-rule"></div>
<p class="abs how-sub">FOR BUSINESSES THAT NEED ACTIONABLE FEEDBACK ON ALL TYPES OF DIGITAL AND PRINT MATERIAL</p>

<div class="abs step" style="left:117px">
  <svg width="110" height="118" viewBox="0 0 110 118">
    <path d="M55 8a45 45 0 1 0 22 84l22 18-9-27A45 45 0 0 0 55 8z" fill="#fff" stroke="#f39a1f" stroke-width="4"/>
    <rect x="34" y="38" width="38" height="30" rx="3" fill="none" stroke="#333" stroke-width="3" transform="rotate(-8 53 53)"/>
    <path d="M53 62l-8-8a5 5 0 0 1 8-6 5 5 0 0 1 8 6z" fill="#f39a1f"/>
  </svg>
  <div class="step-label">POST YOUR PROJECT</div>
</div>
<div class="abs step" style="left:466px">
  <svg width="110" height="118" viewBox="0 0 110 118">
    <path d="M55 8a45 45 0 1 0 22 84l22 18-9-27A45 45 0 0 0 55 8z" fill="#fff" stroke="#333" stroke-width="4"/>
    <g fill="#f39a1f">
      <circle cx="42" cy="40" r="6"/><circle cx="68" cy="40" r="6"/>
      <circle cx="42" cy="64" r="6"/><circle cx="68" cy="64" r="6"/>
      <path d="M48 46l14 12M62 46L48 58" stroke="#f39a1f" stroke-width="3"/>
    </g>
  </svg>
  <div class="step-label">COLLABORATE WITH<br>OUR EXPERTS</div>
</div>
<div class="abs step" style="left:812px">
  <svg width="110" height="118" viewBox="0 0 110 118">
    <path d="M55 8a45 45 0 1 0 22 84l22 18-9-27A45 45 0 0 0 55 8z" fill="#fff" stroke="#333" stroke-width="4"/>
    <rect x="33" y="40" width="44" height="28" rx="3" fill="#f39a1f"/>
    <rect x="47" y="33" width="16" height="8" rx="2" fill="none" stroke="#f39a1f" stroke-width="3"/>
    <rect x="33" y="51" width="44" height="2" fill="#fff"/>
  </svg>
  <div class="step-label">REVISE YOUR MATERIAL</div>
</div>

<aside class="abs types">
  <div class="types-head">PROJECTS TYPES</div>
  <div class="types-item">Ne quo falli detraxit</div>
  <div class="types-item">Ne quo falli detraxit</div>
  <div class="types-item">Ne quo falli detraxit</div>
  <div class="types-item">Ne quo falli detraxit</div>
  <div class="types-item">Ne quo falli detraxit</div>
  <div class="types-item">Ne quo falli detraxit</div>
  <div class="types-item">Ne quo falli detraxit</div>
</aside>

<div class="abs col-label" style="left:502px">PRINT PROJECTS</div>
<div class="abs col-label" style="left:811px">DIGITAL PROJECTS</div>

<div class="abs card-img" style="left:502px;background:linear-gradient(160deg,#eef4fa,#c9dbea 60%,#9db8cf)" role="img" aria-label="Architectural drawing of a building with drafting tools"></div>
<div class="abs card-img" style="left:814px;background:linear-gradient(160deg,#cfcac4,#8e8580 50%,#3d3532)" role="img" aria-label="Hand touching marketing, flyer and social service bubbles"></div>

<h3 class="abs card-title" style="left:502px">Quo ludus scripserit</h3>
<div class="abs card-date" style="left:502px">&#9636; 24 November , 2015</div>
<p class="abs card-text" style="left:502px">Denique vulputate at est. Usu quod forensibus ea, eum ei modo deleniti maiestatis. Vix ea purto ignota nostrud, an tempor aliquid eos.</p>
<div class="abs btn-orange" style="left:502px;top:1637px;width:142px;height:36px">READ MORE</div>

<h3 class="abs card-title" style="left:816px">Quo ludus scripserit</h3>
<div class="abs card-date" style="left:816px">&#9636; 24 November , 2015</div>
<p class="abs card-text" style="left:816px">Denique vulputate at est. Usu quod forensibus ea, eum ei modo deleniti maiestatis. Vix ea purto ignota nostrud, an tempor aliquid eos.</p>
<div class="abs btn-orange" style="left:816px;top:1637px;width:142px;height:36px">READ MORE</div>

<svg class="abs band" viewBox="0 0 1200 510" role="img" aria-label="Workspace photo tinted amber on the left and dark blue on the right">
  <defs>
    <linearGradient id="amber" x1="0" y1="0" x2="1" y2="1">
      <stop offset="0" stop-color="#a46a1f"/>
      <stop offset="1" stop-color="#c98a30"/>
    </linearGradient>
    <linearGradient id="navy" x1="0" y1="0" x2="1" y2="1">
      <stop offset="0" stop-color="#2a3340"/>
      <stop offset="1" stop-color="#12161d"/>
    </linearGradient>
  </defs>
  <path d="M0 9Q600 -9 1200 9V510H0Z" fill="url(#navy)"/>
  <path d="M0 9Q300 0 560 2Q660 250 600 510H0Z" fill="url(#amber)"/>
</svg>

<h2 class="abs band-head" style="left:97px">QUO LUDUS SCRIPSERIT PERSEQUERIS</h2>
<p class="abs band-text" style="left:97px;top:1891px;width:470px">Lorem ipsum dolor sit amet, omnes oblique quo no, audiam tritani facilisis cu duo, reque concludaturque an pro. Commodo saperet vim eu. Eu nibh vidisse pro, facilis accusata ei duo. Quas posse liber pro no.</p>
<p class="abs band-text" style="left:97px;top:1981px;width:470px">Lorem ipsum dolor sit amet, omnes oblique quo no, audiam tritani facilisis cu duo, reque concludaturque an pro. Commodo saperet vim eu. Eu nibh vidisse pro, facilis accusata ei duo. Quas posse liber pro no, diam accumsan incorrupte mei no, mea modo iusto deleniti ad. Vel ea sale apeirian delicata, cum clita nostrum dissentiet ut. Lorem ipsum dolor sit amet, omnes oblique quo no, audiam tritani facilisis cu duo, reque concludaturque an pro. Commodo saperet vim eu. Eu nibh vidisse pro, facilis accusata ei duo. Quas posse liber pro no, diam accumsan incorrupte mei no, mea modo iusto deleniti ad. Vel ea sale apeirian delicata, cum clita nostrum dissentiet ut.</p>

<h2 class="abs band-head" style="left:695px;color:var(--orange)">BENEFITS OF EXPERT FEEDBACK</h2>
<p class="abs band-text" style="left:695px;top:1873px;width:430px">Quo ludus scripserit persequeris te, eos et convenire assentior inciderint. Ridens epicuri hendrerit sit ei, vis at nobis pericula</p>
<ul class="abs benefits">
  <li>Denique vulputate at est.</li>
  <li>Eum ei modo deleniti maiestatis</li>
  <li>Ut per impedit oportere mediocritatem</li>
  <li>Denique vulputate at est.</li>
  <li>Cum ne esse</li>
</ul>
<div class="abs btn-orange" style="left:695px;top:2120px;width:143px;height:37px">READ MORE</div>

<footer class="abs footer"></footer>
<div class="abs copy">© 2015 All rights reserved Pelmora</div>
<div class="abs links">Contact | Careers | Privacy | Terms of Use</div>
<div class="abs social" style="left:880px;background:#3b5b98"></div>
<div class="abs social" style="left:940px;background:#2d9ed6"></div>
<div class="abs social" style="left:1002px;background:#e8731c"></div>
<div class="abs social" style="left:1061px;background:#c9372c"></div>

</body>
</html>
```